Silvermoor Property Development Co.

We need a logo and business card design for a Hong Kong based real estate company, PLX Land. We are want the brand to reflect the owners forward thinking, creative, and trend setting projects, while also reflecting a sense of security and strength. We invest in industrial properties which we convert to co-living or co-working spaces. PLX stands for Greater Bay Area which is the region around southern China including HK, Macau, and 9 other Chinese cities...made up of approx. 68 million people. There are massive infrastructure projects including the bridge to Macau and high-speed rail to SZ and the bridge connecting SZ and Zhongshan.

Target Market(s)

Chinese and western retail investors, as well as institutional investors

Industry/Entity Type

Real Estate Development

Contact Information for Business Card

Dale Whitford
CEO
dale@plxland-example.com
M + 852 9581 4062
F + 852 3864 2217
Suite 2207, The Halvern, 41 Tremont Rd., Central, Hong Kong

Logo Text

plx land (company name) lifestyle property development (underneath)

Colors

Designer to choose colors to be used in the design.

Requirements
Must have
• Details listed above. One side should include the logo and company name...plx land in modern, hip styling with "lifestyle property development"
Nice to have
• Could be a Black card, with metallic purple "plx" and white "land"...but open great design ideas
Should not have
• boring and traditional layout

```html
<!DOCTYPE html>
<html lang="en">
<head>
<meta charset="utf-8">
<title>PLX Land – Business Card</title>
<link rel="stylesheet" href="https://fonts.googleapis.com/css2?family=Oswald:wght@600;700&family=Open+Sans:wght@400;600&family=Cormorant+Garamond:wght@500&display=swap">
<style>
  :root {
    --backdrop: #3a3a3c;
    --card: #0c0c0e;
    --purple: #b523c2;
    --purple-deep: #7c1489;
    --white: #f4f4f4;
    --grey: #bdbdbd;
  }
  * { margin: 0; padding: 0; box-sizing: border-box; }
  html, body { width: 1200px; height: 782px; overflow: hidden; }
  body { background: var(--backdrop); position: relative; font-family: "Open Sans", sans-serif; }

  .card {
    position: absolute;
    width: 560px; height: 320px;
    background: var(--card);
    overflow: hidden;
    box-shadow: 0 10px 30px rgba(0,0,0,.45);
  }
  .card--front { left: 580px; top: 60px; }
  .card--back  { left: 60px;  top: 400px; }

  .card__band { position: absolute; left: 0; bottom: 0; width: 100%; height: 44px; }

  .wordmark {
    font-family: "Oswald", sans-serif;
    font-weight: 700;
    letter-spacing: 1px;
    line-height: 1;
    white-space: nowrap;
  }

  /* front */
  .front__logo { position: absolute; left: 0; right: 0; top: 92px; text-align: center; }
  .front__logo .wordmark { color: var(--white); font-size: 66px; }
  .front__tagline {
    margin-top: 16px;
    font-family: "Cormorant Garamond", serif;
    font-weight: 500;
    font-size: 15px;
    letter-spacing: 2px;
    color: var(--grey);
    text-transform: uppercase;
  }

  /* back */
  .person { position: absolute; left: 34px; top: 30px; }
  .person__name {
    font-family: "Oswald", sans-serif; font-weight: 600;
    font-size: 19px; color: var(--purple); text-transform: uppercase; letter-spacing: .3px;
    line-height: 1.1;
  }
  .person__title { font-size: 12px; color: var(--white); }

  .contact { position: absolute; left: 34px; top: 168px; list-style: none; }
  .contact__item { display: flex; align-items: center; gap: 8px; font-size: 14px; color: var(--white); line-height: 1.45; }
  .contact__item svg { width: 12px; height: 12px; flex: none; }

  .back__logo { position: absolute; left: 300px; top: 110px; }
  .back__logo .wordmark { color: var(--purple); font-size: 54px; }

  .address {
    position: absolute; right: 34px; top: 192px;
    text-align: right; font-size: 15px; line-height: 1.35; color: var(--white);
    font-style: normal;
  }
</style>
</head>
<body>

  <section class="card card--front" aria-label="Business card front">
    <div class="front__logo">
      <div class="wordmark">PLX LAND</div>
      <p class="front__tagline">Lifestyle Property Development</p>
    </div>
    <svg class="card__band" viewBox="0 0 560 44" preserveAspectRatio="none" aria-hidden="true">
      <polygon points="0,10 268,22 256,44 0,44" fill="var(--purple-deep)"/>
      <polygon points="276,22 560,34 560,44 264,44" fill="var(--purple)"/>
      <polygon points="286,16 560,28 560,44 274,44" fill="var(--purple)"/>
    </svg>
  </section>

  <section class="card card--back" aria-label="Business card back">
    <div class="person">
      <p class="person__name">Dale Whitford</p>
      <p class="person__title">CEO</p>
    </div>

    <ul class="contact">
      <li class="contact__item">
        <svg viewBox="0 0 12 12" aria-hidden="true"><rect x="3" y="0.5" width="6" height="11" rx="1" fill="none" stroke="var(--purple)" stroke-width="1.3"/></svg>
        + 852 9581 4062
      </li>
      <li class="contact__item">
        <svg viewBox="0 0 12 12" aria-hidden="true"><rect x="3" y="0" width="6" height="4" fill="var(--purple)"/><rect x="0" y="4" width="12" height="5" rx="1" fill="var(--purple)"/><rect x="3" y="8" width="6" height="4" fill="var(--purple)"/></svg>
        + 852 3864 2217
      </li>
      <li class="contact__item">
        <svg viewBox="0 0 12 12" aria-hidden="true"><rect x="0" y="2" width="12" height="8" fill="var(--purple)"/><polyline points="0,2 6,7 12,2" fill="none" stroke="var(--card)" stroke-width="1.2"/></svg>
        dale@plxland-example.com
      </li>
    </ul>

    <div class="back__logo"><div class="wordmark">PLX LAND</div></div>

    <address class="address">
      Suite 2207, The Halvern<br>
      41 Tremont Rd<br>
      Central, Hong Kong
    </address>

    <svg class="card__band" viewBox="0 0 560 44" preserveAspectRatio="none" aria-hidden="true">
      <polygon points="0,6 262,20 250,44 0,44" fill="var(--purple-deep)"/>
      <polygon points="280,14 560,28 560,44 268,44" fill="var(--purple)"/>
    </svg>
  </section>

</body>
</html>
```